Private Investment Firm Needs PowerPoint Presentation Template

Design PowerPoint template, take Pinebrook-submitted rough presentation draft, and drop it into new template. See attached Project Brief file for more detail.
Updates

Some decent designs have been submitted but they seem to lack the understanding of our target markets. I am hopeful that more time and feedback will result in better results.

Target Market(s)

Private company owners and intermediaries.

Font styles to use
Serif

Colors
3176b5

Requirements
Must have
• See attached Project Brief.
Nice to have
Should not have
• No B2C fluff--this is a B2B project.

```html
<!DOCTYPE html>
<html lang="en">
<head>
<meta charset="utf-8">
<title>Non-Control Capital Questionnaire</title>
<link rel="stylesheet" href="https://fonts.googleapis.com/css2?family=Montserrat:wght@400;500;600;700&family=Mulish:wght@400;500&family=Tinos:wght@400&display=swap">
<style>
  :root{
    --brand:#1a6cc4;
    --brand-dark:#0b4a8c;
    --brand-title:#0d5db8;
    --ink:#333a44;
    --paper:#ffffff;
    --shadow:rgba(20,40,70,.14);
  }
  *{box-sizing:border-box;margin:0;padding:0}
  html,body{width:1200px;height:676px;overflow:hidden;background:var(--brand)}
  .slide{position:relative;width:1200px;height:676px;background:var(--brand);font-family:"Montserrat",Arial,sans-serif;color:var(--ink)}
  .sheet{position:absolute;left:44px;top:0;width:1144px;height:676px;background:var(--paper)}
  .site-url{position:absolute;left:22px;top:420px;transform:translate(-50%,-50%) rotate(-90deg);color:#fff;font-family:"Tinos",serif;font-size:15px;letter-spacing:.3px;white-space:nowrap}
  .page-num{position:absolute;right:22px;top:18px;font-family:"Tinos",serif;font-size:19px;color:#222}
  .slide-title{position:absolute;left:86px;top:22px;font-size:29px;font-weight:700;color:var(--brand-title);letter-spacing:.3px}
  .section-band{position:absolute;left:44px;top:78px;width:1144px;height:42px;background:var(--brand);color:#fff;font-size:29px;font-weight:700;padding-left:42px;line-height:42px;letter-spacing:.3px}
  .section-lede{position:absolute;left:86px;top:128px;font-size:17.5px;font-weight:600;color:var(--brand-title)}
  .card{position:absolute;background:var(--paper);border-radius:38px 0 56px 0;box-shadow:0 4px 14px var(--shadow)}
  .card .question{position:absolute;left:30px;font-family:"Mulish",Arial,sans-serif;font-size:12.2px;line-height:13px;color:var(--brand);font-weight:500;white-space:nowrap}
  .card .question u{text-decoration-thickness:1px}
  .card .points{position:absolute;left:18px;right:26px;list-style:none;font-size:9.2px;line-height:12.8px;letter-spacing:-.05px}
  .card .points li{position:relative;padding-left:12px}
  .card .points li::before{content:"";position:absolute;left:0;top:3.5px;width:5px;height:5px;border:1.6px solid var(--brand);transform:rotate(45deg)}
  .card .points b{font-weight:500;color:var(--brand)}
  .tag{position:absolute;width:92px;height:74px}
  .tag svg{position:absolute;left:0;top:0}
  .tag .tag-label{position:absolute;left:14px;right:0;top:7px;text-align:center;color:#fff;font-size:12.5px;font-weight:500;letter-spacing:.3px}
  .tag .tag-num{position:absolute;left:14px;right:0;top:19px;text-align:center;color:#fff;font-size:30px;font-weight:500}
  .brand-mark{position:absolute;left:68px;top:618px;display:flex;align-items:center;gap:8px;color:var(--brand-dark);font-size:18px;font-weight:600;letter-spacing:1px}
  .brand-mark i{display:block;width:30px;height:30px;border-radius:50%;background:var(--brand)}
</style>
</head>
<body>
<div class="slide">
  <div class="sheet"></div>
  <div class="site-url">www.pinebrookcapital.com</div>
  <div class="page-num">17</div>
  <h1 class="slide-title">NON-CONTROL CAPITAL QUESTIONNAIRE</h1>
  <h2 class="section-band">The Critical Questions to Ask of Any Prospective Non-Control Investor</h2>
  <p class="section-lede">Non-Control Capital is a specialty, so only those firms with deep experience investing it as a team should be considered</p>

  <div class="card" style="left:104px;top:190px;width:284px;height:180px">
    <p class="question" style="top:22px">How many years has the<br>firm been investing<br>Non-Control Capital?</p>
    <ul class="points" style="top:88px">
      <li><b>Best Answer:</b> 5+ years investing as a team within the current firm.</li>
      <li>Indicates comfort and experience evaluating and making NCC investments with each other and increases likelihood of close.</li>
    </ul>
  </div>
  <div class="card" style="left:406px;top:190px;width:284px;height:180px">
    <p class="question" style="top:17px">How may fully-invested<br>Non-Control Capital<br>funds in the firm’s<br>history?</p>
    <ul class="points" style="top:88px">
      <li><b>Best Answer:</b> 2+ fully-invested funds.</li>
      <li>Indicates experience and ability to close deals with the current regime—those firms without it may only be testing the waters and not have a long-term commitment to NCC investing.</li>
    </ul>
  </div>
  <div class="card" style="left:702px;top:190px;width:284px;height:180px">
    <p class="question" style="top:22px">What percentage of the<br>firm’s voting investment<br>committee are full-time<br>Non-Control Capital<br>investors?</p>
    <ul class="points" style="top:103px">
      <li><b>Best Answer:</b> Super-majority.</li>
      <li>Indicates commitment, experience, and focus on NCC and overcomes dependency on buyout heritage, if any.</li>
    </ul>
  </div>

  <div class="card" style="left:98px;top:406px;width:284px;height:180px">
    <p class="question" style="top:28px">What is the number of<br>Non-Control Capital in-<br>vestments made with<br>the <u>current firm and</u></p>
    <ul class="points" style="top:104px">
      <li><b>Best Answer:</b> 20+</li>
      <li>Indicates long-term experience and comfort with current team, investment committee, and NCC investment assessment.</li>
    </ul>
  </div>
  <div class="card" style="left:400px;top:406px;width:284px;height:180px">
    <p class="question" style="top:13px">What percentage of<br>portfolio investments<br>made are “sponsorless”<br>(those without a<br>change-of-control in-</p>
    <ul class="points" style="top:89px">
      <li><b>Best Answer:</b> 80%+ of all investments closed in the last 5 years (assumes current transac-tion is also sponsorless)</li>
      <li>Indicates ability to add-value as a sole minority investor and not simply as a back-up to anoth-er sponsor.</li>
    </ul>
  </div>
  <div class="card" style="left:698px;top:406px;width:438px;height:180px">
    <p class="question" style="top:22px">Can the investor show <u>quantifiable proof</u><br>of their ability to asportfolio companies<br>with growth and improvement<br>(assumes more than 20 <u>exited</u> Non-Control invest-<br>ments)?</p>
    <ul class="points" style="top:98px;right:12px">
      <li><b>Best Answer:</b> Yes (company owners should evaluate investors on actual historical revenue, EBITDA, and employee growth impact and the results should exceed what the current management has achieved on their own over the past 3 years)</li>
      <li>Indicates true value-added ability to help owners grow their businesses. Those with-out proof of their impact, or who are unwilling to disclose it, should be excluded.</li>
    </ul>
  </div>

  <div class="tag" style="left:268px;top:174px">
    <svg width="92" height="74" viewBox="0 0 92 74"><polygon points="0,14 14,0 14,14" fill="var(--brand-dark)"/><polygon points="14,0 92,0 92,70 53,58 14,70" fill="var(--brand)"/><polygon points="60,0 92,0 92,70 53,58" fill="#ffffff" opacity=".07"/></svg>
    <span class="tag-label">QUESTION</span><span class="tag-num">01</span>
  </div>
  <div class="tag" style="left:570px;top:174px">
    <svg width="92" height="74" viewBox="0 0 92 74"><polygon points="0,14 14,0 14,14" fill="var(--brand-dark)"/><polygon points="14,0 92,0 92,70 53,58 14,70" fill="var(--brand)"/><polygon points="60,0 92,0 92,70 53,58" fill="#ffffff" opacity=".07"/></svg>
    <span class="tag-label">QUESTION</span><span class="tag-num">02</span>
  </div>
  <div class="tag" style="left:866px;top:174px">
    <svg width="92" height="74" viewBox="0 0 92 74"><polygon points="0,14 14,0 14,14" fill="var(--brand-dark)"/><polygon points="14,0 92,0 92,70 53,58 14,70" fill="var(--brand)"/><polygon points="60,0 92,0 92,70 53,58" fill="#ffffff" opacity=".07"/></svg>
    <span class="tag-label">QUESTION</span><span class="tag-num">03</span>
  </div>
  <div class="tag" style="left:262px;top:390px">
    <svg width="92" height="74" viewBox="0 0 92 74"><polygon points="0,14 14,0 14,14" fill="var(--brand-dark)"/><polygon points="14,0 92,0 92,70 53,58 14,70" fill="var(--brand)"/><polygon points="60,0 92,0 92,70 53,58" fill="#ffffff" opacity=".07"/></svg>
    <span class="tag-label">QUESTION</span><span class="tag-num">04</span>
  </div>
  <div class="tag" style="left:564px;top:390px">
    <svg width="92" height="74" viewBox="0 0 92 74"><polygon points="0,14 14,0 14,14" fill="var(--brand-dark)"/><polygon points="14,0 92,0 92,70 53,58 14,70" fill="var(--brand)"/><polygon points="60,0 92,0 92,70 53,58" fill="#ffffff" opacity=".07"/></svg>
    <span class="tag-label">QUESTION</span><span class="tag-num">05</span>
  </div>
  <div class="tag" style="left:972px;top:390px">
    <svg width="92" height="74" viewBox="0 0 92 74"><polygon points="0,14 14,0 14,14" fill="var(--brand-dark)"/><polygon points="14,0 92,0 92,70 53,58 14,70" fill="var(--brand)"/><polygon points="60,0 92,0 92,70 53,58" fill="#ffffff" opacity=".07"/></svg>
    <span class="tag-label">QUESTION</span><span class="tag-num">06</span>
  </div>

  <div class="brand-mark"><i></i><span>PINEBROOK CAPITAL</span></div>
</div>
</body>
</html>
```